Sole Relationship Graphic of Chapter Organization for Book

This design shows relationships between variables associated with footwear and footprints. It will be used as a graphic in a book. The four elements of the graphic are (1) Variables, (2) Book Chapter Numbers (which correspond to the relationship(s) between at least two variables, (3) Relationship Arrows, and (4) Influence Arrows (because the influencers affect the variables differently than relationships between the variables). These names simply relate to the attempts I have made (and attached) at creating a graphic. In the attached diagrams, the circles with numbers are placeholders for the book chapter numbers, which may be changed so it will be good if I can change those after the graphic is completed. Chapter 1 will be the introduction.
The intent of of outsourcing this project is not necessarily sticking to the formats I have attached, but to allow your creativity to produce a useful graphic that can visually make the most sense of the relationships between the variables as chapters to readers of the book.

Target Market(s)

Search and Rescue Trackers

Requirements
Must have
• Information listed in project description, and drafted in attached diagrams
Nice to have
• Can include outlines of barefoot and outsoles. While Chapters 1 (Intro), 2 (Missing Persons' Footwear), 10 (Case Studies) and 11 (Summary) are set, the others aren't. The end game of this book is to use the rest of the variables to arrive at the end game, which is measurements for barefoot track length or outsole track length...so those two variables can be highlighted in some way to emphasize their importance.

```html
<!DOCTYPE html>
<html lang="en">
<head>
<meta charset="utf-8">
<title>Footwear and Footprint Variables by Chapter</title>
<link href="https://fonts.googleapis.com/css2?family=Roboto:wght@300;400;500;700&display=swap" rel="stylesheet">
<style>
  :root {
    --ink: #0a0a0a;
    --paper: #ffffff;
    --chapter-blue: #1f4fb0;
    --figure-fill: #f1f1f1;
    --hairline: #3a3a3a;
  }
  html, body {
    margin: 0;
    padding: 0;
    background: var(--paper);
    overflow: hidden;
  }
  .canvas {
    width: 1200px;
    height: 675px;
    position: relative;
    overflow: hidden;
    background: var(--paper);
    font-family: 'Roboto', sans-serif;
  }
  .diagram {
    position: absolute;
    inset: 0;
  }
  .title-text {
    font-family: 'Roboto', sans-serif;
    font-weight: 700;
    font-size: 23px;
    fill: var(--ink);
  }
  .variable-label {
    font-family: 'Roboto', sans-serif;
    font-weight: 300;
    font-size: 13px;
    fill: var(--ink);
  }
  .chapter-ring {
    fill: var(--paper);
    stroke: var(--chapter-blue);
    stroke-width: 2;
  }
  .chapter-number {
    font-family: 'Roboto', sans-serif;
    font-weight: 500;
    font-size: 17px;
    fill: var(--ink);
  }
  .relation {
    fill: none;
    stroke: var(--ink);
    stroke-width: 4;
  }
  .influence {
    fill: none;
    stroke: var(--ink);
    stroke-width: 4;
    stroke-dasharray: 4 4;
  }
  .dimension {
    fill: none;
    stroke: var(--hairline);
    stroke-width: 0.6;
  }
  .result-box {
    fill: var(--paper);
    stroke: var(--ink);
    stroke-width: 2.5;
  }
  .legend-heading {
    font-family: 'Roboto', sans-serif;
    font-weight: 500;
    font-size: 20px;
    fill: var(--ink);
  }
  .legend-text {
    font-family: 'Roboto', sans-serif;
    font-weight: 300;
    font-size: 17px;
    fill: var(--ink);
  }
</style>
</head>
<body>
<div class="canvas">
<svg class="diagram" width="1200" height="675" viewBox="0 0 1200 675" xmlns="http://www.w3.org/2000/svg">
  <defs>
    <marker id="head" markerUnits="userSpaceOnUse" viewBox="0 0 12 12" markerWidth="12" markerHeight="12" refX="9" refY="6" orient="auto-start-reverse">
      <path d="M3,1 L9,6 L3,11" fill="none" stroke="#0a0a0a" stroke-width="2.2"/>
    </marker>
    <marker id="tick" markerUnits="userSpaceOnUse" viewBox="0 0 8 8" markerWidth="8" markerHeight="8" refX="7" refY="4" orient="auto-start-reverse">
      <path d="M2,1 L7,4 L2,7" fill="none" stroke="#3a3a3a" stroke-width="0.8"/>
    </marker>
  </defs>

  <!-- Heading group -->
  <g class="topic">
    <text class="title-text" x="109" y="232">Missing</text>
    <text class="title-text" x="109" y="260">Persons’</text>
    <text class="title-text" x="109" y="287">Footwear</text>
    <path class="influence" d="M215,252 H263" marker-end="url(#head)"/>
    <path d="M355,107 C325,112 310,135 313,170 C316,200 328,225 318,240 C312,248 298,250 287,252 C298,254 312,256 318,264 C328,279 316,304 313,334 C310,369 325,392 355,398 L355,394 C333,388 326,368 329,336 C332,306 340,281 330,266 C322,256 308,254 298,252 C308,250 322,248 330,238 C340,223 332,198 329,168 C326,136 333,116 355,111 Z" fill="#0a0a0a"/>
  </g>

  <!-- Footwear figure area -->
  <rect x="473" y="155" width="371" height="206" rx="40" fill="var(--figure-fill)" role="img" aria-label="Line drawing of a hiking boot in side view"/>

  <!-- Dimension guides -->
  <g class="dimensions">
    <path class="dimension" d="M472,89 V335"/>
    <path class="dimension" d="M844,89 V356"/>
    <path class="dimension" d="M474,103 H606" marker-start="url(#tick)"/>
    <path class="dimension" d="M707,103 H842" marker-end="url(#tick)"/>
    <path class="dimension" d="M479,267 V412"/>
    <path class="dimension" d="M808,309 V412"/>
    <path class="dimension" d="M481,400 H624" marker-start="url(#tick)"/>
    <path class="dimension" d="M717,400 H806" marker-end="url(#tick)"/>
    <path class="dimension" d="M867,206 H914"/>
    <path class="dimension" d="M867,314 H914"/>
    <path class="dimension" d="M891,240 V208" marker-end="url(#tick)"/>
    <path class="dimension" d="M891,270 V312" marker-end="url(#tick)"/>
  </g>

  <!-- Relationship lines -->
  <g class="relations">
    <path class="relation" d="M435,260 V67 H645 V89" marker-end="url(#head)"/>
    <path class="relation" d="M435,260 V437 H666 V417" marker-end="url(#head)"/>
    <path class="relation" d="M982,133 H673 V117" marker-start="url(#head)" marker-end="url(#head)"/>
    <path class="relation" d="M646,187 H689 V248" marker-start="url(#head)" marker-end="url(#head)"/>
    <path class="relation" d="M607,206 V298 H666 V387" marker-start="url(#head)" marker-end="url(#head)"/>
    <path class="relation" d="M692,286 V387" marker-start="url(#head)" marker-end="url(#head)"/>
    <path class="relation" d="M734,253 H864" marker-start="url(#head)" marker-end="url(#head)"/>
    <path class="relation" d="M734,276 H823 V389 H982" marker-start="url(#head)" marker-end="url(#head)"/>
  </g>

  <!-- Influence lines -->
  <g class="influences">
    <path class="influence" d="M647,118 V133 H513 V158" marker-start="url(#head)" marker-end="url(#head)"/>
    <path class="influence" d="M548,185 H583" marker-start="url(#head)" marker-end="url(#head)"/>
    <path class="influence" d="M513,211 V324 H645 V387" marker-start="url(#head)" marker-end="url(#head)"/>
    <path class="influence" d="M692,417 V437 H782" marker-start="url(#head)" marker-end="url(#head)"/>
  </g>

  <!-- Variables -->
  <g class="variables">
    <text class="variable-label" x="658" y="108" text-anchor="middle">Outsole Length</text>
    <text class="variable-label" x="512" y="180" text-anchor="middle">Individual</text>
    <text class="variable-label" x="512" y="195" text-anchor="middle">Variation</text>
    <text class="variable-label" x="612" y="180" text-anchor="middle">Nominal</text>
    <text class="variable-label" x="612" y="195" text-anchor="middle">Size</text>
    <text class="variable-label" x="689" y="272" text-anchor="middle">Barefoot</text>
    <text class="variable-label" x="891" y="260" text-anchor="middle">Height</text>
    <text class="variable-label" x="672" y="405" text-anchor="middle">Insole Length</text>
    <text class="variable-label" x="792" y="442">Hook Area</text>
  </g>

  <!-- Result measurements -->
  <g class="results">
    <rect class="result-box" x="992" y="116" width="147" height="34"/>
    <text class="variable-label" x="1008" y="138">Shod Track Length</text>
    <rect class="result-box" x="992" y="373" width="147" height="33"/>
    <text class="variable-label" x="1004" y="394">Barefoot Track Length</text>
  </g>

  <!-- Chapter markers -->
  <g class="chapters">
    <g class="chapter"><circle class="chapter-ring" cx="435" cy="260" r="16"/><text class="chapter-number" x="435" y="266" text-anchor="middle">5</text></g>
    <g class="chapter"><circle class="chapter-ring" cx="588" cy="133" r="16"/><text class="chapter-number" x="588" y="139" text-anchor="middle">7</text></g>
    <g class="chapter"><circle class="chapter-ring" cx="818" cy="133" r="16"/><text class="chapter-number" x="818" y="139" text-anchor="middle">6</text></g>
    <g class="chapter"><circle class="chapter-ring" cx="564" cy="213" r="16"/><text class="chapter-number" x="564" y="219" text-anchor="middle">5</text></g>
    <g class="chapter"><circle class="chapter-ring" cx="689" cy="214" r="16"/><text class="chapter-number" x="689" y="220" text-anchor="middle">4</text></g>
    <g class="chapter"><circle class="chapter-ring" cx="794" cy="252" r="16"/><text class="chapter-number" x="794" y="258" text-anchor="middle">8</text></g>
    <g class="chapter"><circle class="chapter-ring" cx="635" cy="298" r="16"/><text class="chapter-number" x="635" y="304" text-anchor="middle">4</text></g>
    <g class="chapter"><circle class="chapter-ring" cx="560" cy="323" r="16"/><text class="chapter-number" x="560" y="329" text-anchor="middle">7</text></g>
    <g class="chapter"><circle class="chapter-ring" cx="692" cy="339" r="16"/><text class="chapter-number" x="692" y="345" text-anchor="middle">9</text></g>
    <g class="chapter"><circle class="chapter-ring" cx="851" cy="389" r="16"/><text class="chapter-number" x="851" y="395" text-anchor="middle">9</text></g>
    <g class="chapter"><circle class="chapter-ring" cx="731" cy="437" r="16"/><text class="chapter-number" x="731" y="443" text-anchor="middle">3</text></g>
  </g>

  <!-- Legend -->
  <g class="legend">
    <text class="legend-heading" x="71" y="504">LEGEND</text>
    <path d="M71,511 H259" stroke="#0a0a0a" stroke-width="1.5"/>
    <circle class="chapter-ring" cx="106" cy="538" r="16"/>
    <text class="chapter-number" x="106" y="544" text-anchor="middle">5</text>
    <text class="legend-text" x="141" y="544">Chapter #</text>
    <path class="relation" d="M79,570 H126" marker-start="url(#head)" marker-end="url(#head)"/>
    <text class="legend-text" x="141" y="576">Relationship to</text>
    <path class="influence" d="M79,601 H126" marker-start="url(#head)" marker-end="url(#head)"/>
    <text class="legend-text" x="141" y="607">Influence on</text>
  </g>
</svg>
</div>
</body>
</html>
```